Pharmacy ad

need 2 pharmacy ads for the phone book. one for Brookvale Pharmacy and one for Cedarline Care Pharmacy. Dimensions for ad is 4.75in x 4.667 in. please see attached examples of ad uploaded as well logos of each pharmacy

```html
<!DOCTYPE html>
<html lang="en">
<head>
<meta charset="utf-8">
<title>Pharmacy Ads – Brookvale &amp; Cedarline Care</title>
<link rel="stylesheet" href="https://fonts.googleapis.com/css2?family=Barlow:wght@400;500;600;700;800;900&family=Barlow+Condensed:wght@600;700&family=Kaushan+Script&display=swap">
<style>
  :root{
    --backdrop:#fdf4a6;
    --navy:#1f1d4f;
    --ink:#1b1b2b;
    --blue:#3a4fa8;
    --sky:#8fc8e8;
    --sky-light:#d6ecf7;
    --green:#7cc043;
    --green-light:#c9e39a;
    --green-deep:#5fa82e;
    --white:#ffffff;
  }
  *{box-sizing:border-box;margin:0;padding:0}
  html,body{width:1200px;height:600px;overflow:hidden;background:var(--backdrop)}
  body{position:relative;font-family:"Barlow",Arial,sans-serif;color:var(--ink)}

  .ad{position:absolute;top:22px;width:566px;height:556px;overflow:hidden;box-shadow:0 1px 3px rgba(0,0,0,.35)}
  .ad--brookvale{left:20px;background:linear-gradient(160deg,#a9d6ee 0%,var(--sky) 55%,#7cbfe3 100%)}
  .ad--cedarline{left:612px;background:var(--white)}
  .layer{position:absolute;left:0;top:0}
  .abs{position:absolute}

  /* ---------- Brookvale ---------- */
  .bv-discount{left:0;top:22px;width:272px;text-align:center;color:var(--navy)}
  .bv-discount .pct{font-weight:900;font-size:72px;line-height:.85}
  .bv-discount .word{font-weight:800;font-size:39px;line-height:.95;letter-spacing:.5px}
  .bv-offers{left:20px;top:112px;width:232px;text-align:center;color:var(--navy);font-size:15px;line-height:1.02}
  .bv-offers .offer{padding:8px 0 9px}
  .bv-offers .offer b{font-weight:800;display:block}
  .bv-offers .offer + .offer{border-top:3px dotted var(--navy)}
  .bv-brand{left:300px;top:60px;width:260px;text-align:center;color:var(--navy)}
  .bv-brand .dot{width:96px;height:96px;border-radius:50%;background:var(--green);margin:0 auto 14px}
  .bv-brand .name{font-weight:800;font-size:40px;line-height:1;letter-spacing:1px}
  .bv-brand .tag{font-style:italic;font-size:15px;color:var(--green-deep);margin-top:8px}
  .bv-services{left:26px;top:300px;width:300px;display:grid;grid-template-columns:146px 1fr;column-gap:6px;font-weight:700;font-size:13px;line-height:1.05;color:var(--ink)}
  .bv-services ul{list-style:none}
  .bv-services li{position:relative;padding-left:12px;margin-bottom:8px}
  .bv-services li::before{content:"";position:absolute;left:0;top:4px;width:6px;height:6px;background:var(--ink);transform:rotate(45deg)}
  .bv-rule{left:20px;top:412px;width:390px;border-top:3px dotted var(--ink)}
  .bv-email{left:26px;top:426px;font-size:14px;font-weight:500}
  .bv-branch{top:456px;font-size:12.5px;font-weight:700;line-height:1.1}
  .bv-branch--town{left:26px;width:230px}
  .bv-branch--harbour{left:264px;width:180px;border-left:2px solid var(--ink);padding-left:14px;height:84px}
  .bv-branch .note{font-weight:500;font-size:11px;display:block}
  .bv-branch .line{display:flex;align-items:flex-start;gap:5px;margin-bottom:3px}
  .bv-branch .hours{font-size:13px;margin-top:8px;line-height:1.15}
  .icon{flex:none}

  .payments .card{position:absolute;display:flex;align-items:center;justify-content:center;font-weight:800;font-size:11px;color:var(--navy);background:var(--white);border:1px solid #c9c9c9}

  .social{text-align:center;font-size:13px}
  .social .circle{width:46px;height:46px;border-radius:50%;background:var(--blue);margin:6px auto 3px}
  .social .net{font-weight:700;font-size:11px;color:var(--blue)}

  /* ---------- Cedarline ---------- */
  .cl-photo{left:0;top:0;width:566px;height:230px;background:linear-gradient(90deg,#eef3f6 0%,#dfe6ea 40%,#b9b2ab 70%,#7a5b45 100%)}
  .cl-brand{left:26px;top:26px;display:flex;align-items:center;gap:12px;color:var(--blue)}
  .cl-brand .dot{width:64px;height:64px;border-radius:50%;background:var(--green)}
  .cl-brand .name{font-weight:700;font-size:34px;line-height:1}
  .cl-brand .sub{font-weight:700;font-size:18px;letter-spacing:1px;color:var(--blue);text-align:center;border-top:2px solid var(--green);margin-top:4px;padding-top:2px}
  .cl-accept{left:78px;top:130px;font-weight:800;font-size:12px;color:var(--navy)}
  .cl-slogan{left:0;top:222px;width:566px;text-align:center;font-family:"Kaushan Script",cursive;font-size:48px;color:var(--blue);line-height:1}
  .cl-discount{left:36px;top:304px;color:var(--blue)}
  .cl-discount .pct{font-weight:800;font-size:64px;line-height:.8}
  .cl-discount .word{font-weight:400;font-size:42px;line-height:1;letter-spacing:1px}
  .cl-discount .offers{font-family:"Barlow Condensed",Arial,sans-serif;font-weight:700;font-size:15px;line-height:19px;letter-spacing:.4px}
  .cl-divider{left:270px;top:313px;width:3px;height:141px;background:var(--green)}
  .cl-services{left:286px;top:326px;width:276px;display:grid;grid-template-columns:140px 1fr;color:var(--blue);font-size:13px;line-height:1.1}
  .cl-services ul{list-style:none}
  .cl-services li{position:relative;padding-left:11px;margin-bottom:8px}
  .cl-services ul + ul li{margin-bottom:14px}
  .cl-services li::before{content:"";position:absolute;left:0;top:5px;width:5px;height:5px;border-radius:50%;background:var(--blue)}
  .cl-footer{left:0;top:464px;width:566px;height:92px;background:var(--green)}
  .cl-contact{left:30px;top:474px;font-weight:700;font-size:15px;color:var(--ink)}
  .cl-contact .line{display:flex;align-items:center;gap:8px;margin-bottom:5px}
  .cl-contact .hours{font-size:22px;font-weight:800;margin-top:4px}
  .cl-phone{margin-left:26px;display:inline-flex;align-items:center;gap:8px}
</style>
</head>
<body>

<!-- Brookvale Pharmacy ad -->
<section class="ad ad--brookvale" aria-label="Brookvale Pharmacy advertisement">
  <svg class="layer" width="566" height="556" viewBox="0 0 566 556" aria-hidden="true">
    <defs>
      <radialGradient id="bvGlow" cx="50%" cy="50%" r="50%">
        <stop offset="0" stop-color="#ffffff" stop-opacity=".95"/>
        <stop offset=".75" stop-color="#eef7fc" stop-opacity=".9"/>
        <stop offset="1" stop-color="#d6ecf7" stop-opacity=".85"/>
      </radialGradient>
      <linearGradient id="bvGreen" x1="0" y1="0" x2="1" y2="1">
        <stop offset="0" stop-color="#b5dc7a"/>
        <stop offset="1" stop-color="#d6eba9"/>
      </linearGradient>
    </defs>
    <circle cx="440" cy="150" r="205" fill="url(#bvGlow)"/>
    <path d="M0,282 H296 C328,282 338,300 348,330 C368,392 430,408 566,408 V556 H0Z" fill="url(#bvGreen)"/>
  </svg>

  <div class="abs bv-discount">
    <div class="pct">10%</div>
    <div class="word">DISCOUNT</div>
  </div>
  <div class="abs bv-offers">
    <div class="offer">ON SENIOR CITIZEN<b>FOR PATIENTS<br>60 YEARS AND OVER</b></div>
    <div class="offer">ON STUDENT<b>WITH VALID ID CARD</b></div>
    <div class="offer">ON HOSPITAL<b>PRESCRIPTIONS</b></div>
  </div>

  <div class="abs bv-brand">
    <div class="dot"></div>
    <div class="name">BROOKVALE<br>PHARMACY</div>
    <div class="tag">We Care About Your Health</div>
  </div>

  <div class="payments">
    <div class="card" style="left:370px;top:309px;width:49px;height:30px">Paylane</div>
    <div class="card" style="left:434px;top:309px;width:50px;height:30px">CardMax</div>
    <div class="card" style="left:497px;top:309px;width:45px;height:30px;font-size:10px">Sagewell</div>
    <div class="card" style="left:400px;top:349px;width:115px;height:23px">Norvica</div>
  </div>

  <div class="abs bv-services">
    <ul>
      <li>Certified Pharmacists</li>
      <li>Affordable prices</li>
      <li>Brand and Generic Medicines</li>
      <li>Blood Pressure and Glucose checks</li>
    </ul>
    <ul>
      <li>Personal care and Beauty Products</li>
      <li>Injectables</li>
      <li>Special Orders</li>
      <li>Delivery service</li>
    </ul>
  </div>

  <div class="abs bv-rule"></div>
  <div class="abs bv-email">For more inquiries, email us: hello@brookvalerx.com</div>

  <div class="abs bv-branch bv-branch--town">
    <div class="line">
      <svg class="icon" width="9" height="12" viewBox="0 0 10 14"><path d="M5 0a5 5 0 0 1 5 5c0 4-5 9-5 9S0 9 0 5a5 5 0 0 1 5-5zm0 3a2 2 0 1 0 0 4 2 2 0 0 0 0-4z" fill="currentColor"/></svg>
      <span>42 Larch Street, Marlow Bay<span class="note">(opposite Grace Hill Chapel)</span></span>
    </div>
    <div class="line">
      <svg class="icon" width="14" height="11" viewBox="0 0 16 12"><path d="M1 4c0-3 14-3 14 0v2h-4V4H5v2H1zM3 7h10l1 5H2z" fill="currentColor"/></svg>
      <span>1 555 210 4418</span>
    </div>
    <div class="hours">MONDAY – FRIDAY 10AM TO 6PM<br>SATURDAY 10AM TO 5PM</div>
  </div>

  <div class="abs bv-branch bv-branch--harbour">
    <div class="line">
      <svg class="icon" width="9" height="12" viewBox="0 0 10 14"><path d="M5 0a5 5 0 0 1 5 5c0 4-5 9-5 9S0 9 0 5a5 5 0 0 1 5-5zm0 3a2 2 0 1 0 0 4 2 2 0 0 0 0-4z" fill="currentColor"/></svg>
      <span>Harbour Walk, Food Court, Marlow Bay</span>
    </div>
    <div class="line">
      <svg class="icon" width="14" height="11" viewBox="0 0 16 12"><path d="M1 4c0-3 14-3 14 0v2h-4V4H5v2H1zM3 7h10l1 5H2z" fill="currentColor"/></svg>
      <span>1 555 210 4472</span>
    </div>
    <div class="hours">MONDAY – SATURDAY<br>9AM TO 5PM</div>
  </div>

  <div class="abs social" style="left:460px;top:462px;width:90px">
    <div>Visit us on</div>
    <div class="circle"></div>
    <div class="net">Friendbook</div>
  </div>
</section>

<!-- Cedarline Care Pharmacy ad -->
<section class="ad ad--cedarline" aria-label="Cedarline Care Pharmacy advertisement">
  <div class="abs cl-photo" role="img" aria-label="Photo of a pharmacist in a white coat holding a medicine box in a pharmacy"></div>

  <svg class="layer" width="566" height="556" viewBox="0 0 566 556" aria-hidden="true">
    <path d="M0,170 C140,200 330,210 566,170 V300 C400,272 170,272 0,300Z" fill="var(--green-light)"/>
    <path d="M0,160 C140,196 330,204 566,162 V176 C330,214 140,210 0,182Z" fill="var(--green)"/>
    <path d="M0,296 C170,268 400,268 566,296 V304 C400,278 170,278 0,306Z" fill="var(--blue)"/>
  </svg>

  <div class="abs cl-brand">
    <div class="dot"></div>
    <div>
      <div class="name">Cedarline Care</div>
      <div class="sub">PHARMACY</div>
    </div>
  </div>

  <div class="abs cl-accept">WE ACCEPT:</div>
  <div class="payments">
    <div class="card" style="left:78px;top:145px;width:44px;height:28px">Paylane</div>
    <div class="card" style="left:132px;top:145px;width:44px;height:28px">CardMax</div>
    <div class="card" style="left:185px;top:145px;width:36px;height:28px;font-size:8px">Sagewell</div>
    <div class="card" style="left:226px;top:147px;width:114px;height:24px">Norvica</div>
  </div>

  <div class="abs cl-slogan">Where good health begins</div>

  <div class="abs cl-discount">
    <div class="pct">10%</div>
    <div class="word">DISCOUNT</div>
    <div class="offers">ON SENIOR CITIZEN<br>ON STUDENT WITH VALID ID CARD<br>ON HOSPITAL PRESCRIPTIONS</div>
  </div>

  <div class="abs cl-divider"></div>
  <div class="abs cl-services">
    <ul>
      <li>Certified Pharmacists</li>
      <li>Affordable prices</li>
      <li>Brand and<br>Generic Medicines</li>
      <li>Blood Pressure and<br>Glucose checks</li>
    </ul>
    <ul>
      <li>Personal care and<br>Beauty Products</li>
      <li>Injectables</li>
      <li>Special Orders</li>
      <li>Delivery service</li>
    </ul>
  </div>

  <div class="abs cl-footer"></div>
  <div class="abs cl-contact">
    <div class="line">
      <svg class="icon" width="13" height="18" viewBox="0 0 10 14"><path d="M5 0a5 5 0 0 1 5 5c0 4-5 9-5 9S0 9 0 5a5 5 0 0 1 5-5zm0 3a2 2 0 1 0 0 4 2 2 0 0 0 0-4z" fill="var(--blue)"/></svg>
      <span>Unit B4, Tidewater Arcade, Shore Road, Marlow Bay</span>
    </div>
    <div class="line">
      <svg class="icon" width="20" height="14" viewBox="0 0 20 14"><rect x="1" y="1" width="18" height="12" fill="none" stroke="var(--blue)" stroke-width="2"/><path d="M1 1l9 7 9-7" fill="none" stroke="var(--blue)" stroke-width="2"/></svg>
      <span>care@cedarlinerx.com</span>
      <span class="cl-phone">
        <svg class="icon" width="20" height="15" viewBox="0 0 16 12"><path d="M1 4c0-3 14-3 14 0v2h-4V4H5v2H1zM3 7h10l1 5H2z" fill="var(--blue)"/></svg>
        1 555 318 6620
      </span>
    </div>
    <div class="hours">MONDAY – SATURDAY 8AM TO 7PM</div>
  </div>

  <div class="abs social" style="left:460px;top:474px;width:90px">
    <div>Visit us on</div>
    <div class="circle" style="background:var(--blue)"></div>
    <div class="net" style="color:var(--ink)">Friendbook</div>
  </div>
</section>

</body>
</html>
```